Granite Tile Retail Website

We need wireframe PSD for a website selling granite tile. There are 4 custom pages, shopping cart page, and checkout page. I have a logo designed but the color scheme is up to you.
Color Gallery - We have approximately 20 different stone colors. Each color will have a little gallery of its own pictures. On this page the customer can also add a sample piece of the color they are viewing to their shopping cart.
Questions Page - This page has 3 elements
1. Upload or fax diagram of kitchen for quotation
2. Installation video
3. Installation FAQ (text)
Order Page - This page has 3 steps for the customer
1. Customer chooses his color.
2. For each color we have numerous different products. He inputs the quantity of each product.
3. Customer is given total price and shipping quote. If order over $500 it says "This order qualifies for free shipping". Customer can click on button to "Order Now"
Shopping Cart - Very standard, just like I have attached here. Just modify for your colors / font.
Checkout - Just like in the attached. See design-explanation.docx for minor adjustments.
I have vector file for logo.
Updates
Please try to post your designs by tonightÂ
Target Market(s)
Home owners 40-60 years old
Industry/Entity Type
Shopping
Look and feel

```html
<!DOCTYPE html>
<html lang="en">
<head>
<meta charset="utf-8">
<title>Stoneway Tile – Shopping Cart</title>
<link rel="stylesheet" href="https://fonts.googleapis.com/css2?family=Oswald:wght@500;600&family=Open+Sans:wght@400;600&display=swap">
<style>
:root{
  --page-bg:#f4f4f4;
  --panel-bg:#ffffff;
  --band-bg:#f2f2f2;
  --row-alt:#f0f0f0;
  --rule:#d6d6d6;
  --maroon:#5a1f2e;
  --gold:#e6a84a;
  --gold-dark:#c98a2c;
  --ink:#3a3a3a;
  --muted:#555;
  --dark-btn:#2a2520;
}
*{box-sizing:border-box;margin:0;padding:0}
html,body{width:997px;height:1200px;overflow:hidden}
body{background:var(--page-bg);font-family:"Open Sans",sans-serif;color:var(--ink);position:relative}
.page{position:absolute;left:37px;top:37px;width:923px;height:1126px;background:var(--panel-bg);border:1px solid #e6e6e6}
.abs{position:absolute}
.header{left:18px;top:23px;width:886px;height:109px;background:linear-gradient(#fff,var(--band-bg));border-top:1px solid #e4e4e4;border-bottom:1px solid #e0e0e0}
.brand{left:28px;top:28px;display:flex;align-items:center;gap:10px;font-family:"Oswald",sans-serif;font-weight:600;font-size:38px;line-height:50px;color:var(--maroon);letter-spacing:2px;white-space:nowrap}
.brand-mark{width:26px;height:26px;background:var(--gold)}
.nav{right:28px;top:28px;display:flex;font-family:"Oswald",sans-serif;font-weight:500;font-size:18px;color:#3f3f3f;white-space:nowrap}
.nav span{padding:0 9px;border-left:1px solid #555;line-height:54px}
.nav span:first-child{border-left:none}
.nav .current{color:var(--gold)}
.title{left:29px;top:170px;font-family:"Oswald",sans-serif;font-weight:500;font-size:24px;line-height:30px;color:#3c3c3c}
.cart{left:18px;top:218px;width:886px;border-collapse:collapse;table-layout:fixed}
.cart th{font-family:"Oswald",sans-serif;font-weight:500;font-size:15px;line-height:20px;color:var(--maroon);text-align:left;height:21px;padding:0 0 0 8px;border-left:1px solid var(--rule);border-bottom:1px solid var(--rule);white-space:nowrap}
.cart th:first-child,.cart td:first-child{border-left:none;padding-left:0}
.cart td{height:99px;vertical-align:top;border-left:1px solid var(--rule);border-bottom:1px solid #e2e2e2;padding:14px 12px;font-size:14px;color:var(--muted);white-space:nowrap}
.cart tr:nth-child(odd) td{background:var(--row-alt)}
.cart td.pic{padding:4px 8px 0 0;background:#fff!important}
.swatch{width:137px;height:88px;border:2px solid rgba(0,0,0,.35)}
.name{font-size:16px;color:#444;border-bottom:1px solid #666;padding-bottom:1px}
.qty{display:block;margin:0 auto;width:38px;height:24px;border:1px solid #bbb;background:#fff}
.btn-dark{top:737px;height:30px;background:var(--dark-btn);border:2px solid #111;font-family:"Oswald",sans-serif;font-weight:500;font-size:17px;color:var(--gold);display:flex;align-items:center;justify-content:center;white-space:nowrap}
.rule{left:18px;top:771px;width:886px;border-top:1px solid var(--rule)}
.totals{right:37px;top:819px;text-align:right;font-size:15px;color:#444;line-height:19px;white-space:nowrap}
.grand{right:37px;top:866px;font-size:19px;line-height:26px;font-weight:600;color:#444;display:flex;gap:64px;white-space:nowrap}
.checkout{left:603px;top:914px;width:301px;height:52px;background:linear-gradient(#eeb458,var(--gold-dark));border:2px solid #d39436;display:flex;align-items:center;gap:12px;padding-left:14px;font-family:"Oswald",sans-serif;font-weight:500;font-size:23px;line-height:1;color:#2b1d14;white-space:nowrap;overflow:hidden}
.footer{left:18px;top:1009px;width:886px;height:101px;background:linear-gradient(var(--band-bg),#fff);border-top:1px solid #e2e2e2}
.fcol{top:13px;font-family:"Oswald",sans-serif;font-weight:500;font-size:13px;line-height:17.6px;color:var(--maroon);white-space:nowrap}
.fcol .current{color:var(--gold)}
.badge-seal{left:676px;top:18px;width:68px;height:64px;border-radius:50%;background:#d8b53a}
.badge-box{left:766px;top:13px;width:106px;height:40px;background:#155b7e;border-radius:3px}
.badge-bar{left:766px;top:60px;width:106px;height:30px;background:#1c3f84;border-radius:3px}
</style>
</head>
<body>
<div class="page">
  <div class="abs header">
    <div class="abs brand"><span class="brand-mark"></span>STONEWAY TILE</div>
    <nav class="abs nav"><span>HOME</span><span>GALLERY</span><span>QUESTIONS</span><span>ORDER</span><span class="current">SHOPPING CART</span></nav>
  </div>

  <h1 class="abs title">SHOPPING CART</h1>

  <table class="abs cart">
    <colgroup><col style="width:145px"><col style="width:361px"><col style="width:157px"><col style="width:102px"><col style="width:121px"></colgroup>
    <thead><tr><th>PRICTURE</th><th>PRODUCT NAME</th><th>UNIT PRICE</th><th>QTY</th><th>SUBTOTAL</th></tr></thead>
    <tbody>
      <tr><td class="pic"><div class="swatch" style="background:#a57a58" role="img" aria-label="Giallo stone swatch"></div></td><td><span class="name">Giallo color name</span></td><td>$ 4.99</td><td><span class="qty"></span></td><td>$ 4.99</td></tr>
      <tr><td class="pic"><div class="swatch" style="background:#f1e0d2;border-color:#d8bfa8" role="img" aria-label="Mert Brown stone swatch"></div></td><td><span class="name">Mert Brown color name</span></td><td>$ 4.99</td><td><span class="qty"></span></td><td>$ 4.99</td></tr>
      <tr><td class="pic"><div class="swatch" style="background:#3b3a2c;border-color:#111" role="img" aria-label="Dark olive stone swatch"></div></td><td><span class="name">Something Other color name</span></td><td>$ 4.99</td><td><span class="qty"></span></td><td>$ 4.99</td></tr>
      <tr><td class="pic"><div class="swatch" style="background:#262a33;border-color:#0d0d0d" role="img" aria-label="Dark blue-black stone swatch"></div></td><td><span class="name">Anything New color name</span></td><td>$ 4.99</td><td><span class="qty"></span></td><td>$ 4.99</td></tr>
      <tr><td class="pic"><div class="swatch" style="background:#a57a58" role="img" aria-label="Giallo stone swatch"></div></td><td><span class="name">Giallo color name</span></td><td>$ 4.99</td><td><span class="qty"></span></td><td>$ 4.99</td></tr>
    </tbody>
  </table>

  <div class="abs btn-dark" style="left:18px;width:175px">CONTINUE SHOPPING</div>
  <div class="abs btn-dark" style="left:712px;width:192px">UPDATE SHOPPING CART</div>
  <div class="abs rule"></div>

  <div class="abs totals">Subtotal:&nbsp;&nbsp;&nbsp;&nbsp;&nbsp;&nbsp;$ 214.99<br>Tax:&nbsp;&nbsp;&nbsp;&nbsp;&nbsp;&nbsp;&nbsp;&nbsp;$ 1.09</div>
  <div class="abs grand"><span>Gand total:</span><span>$ 224.09</span></div>

  <div class="abs checkout">
    <svg width="32" height="32" viewBox="0 0 32 32" aria-hidden="true"><circle cx="16" cy="16" r="15" fill="#2b1d14"/><path d="M9 16.5l4.5 4.5L23 11.5" stroke="#fff" stroke-width="3" fill="none" stroke-linecap="round" stroke-linejoin="round"/></svg>
    <span>PROCEED TO CHECKOUT</span>
  </div>

  <footer class="abs footer">
    <div class="abs fcol" style="left:29px">HOME<br>GALLERY<br>QUESTIONS<br>ORDER<br><span class="current">SHOPPING CART</span></div>
    <div class="abs fcol" style="left:226px">RETURN POLICY<br>SHIPPING POLICY<br>PRIVACY<br>TERMS OF USE<br>CUSTOMER SERVICE</div>
    <div class="abs fcol" style="left:443px">NEW LINK<br>ANOTHER LINK<br>THIRD LINK<br>FOURTH LINK<br>FIFTH LINK</div>
    <div class="abs badge-seal" role="img" aria-label="Verified merchant seal"></div>
    <div class="abs badge-box" role="img" aria-label="Accredited business badge"></div>
    <div class="abs badge-bar" role="img" aria-label="Secure payment badge"></div>
  </footer>
</div>
</body>
</html>
```